Business card for denture clinic Veltrimora

We need a new business card with our new logo. We are a denture clinic in New Zealand with our target market being 45+ years old. We would need a space on the back to write our patients next appointment on. We would space for only one appointment rather than a list. We will attach a photo showing an example of this. But of course, we would like to see your twist on this. We want it to be bold and easy to read and a good mixture of professional but modern. We have attached our logo to be used on the card.

Target Market(s)

People aged 45+ needing dentures

Industry/Entity Type

Dental

Contact Information for Business Card

We want our logo on the front and the space to write an appointment on the back. I've attached an example our our old business card showing this. We need to have the technicians details on the front.

Font styles to use
Sans Serif

Colors
0255a3
919191
fbfbfb

Requirements
Must have
• The following details:
• Liam Dorsett BDT, PGDipCDentTech Calverin
• Dental Prosthetist
• Phone numbers: 0800 47 3125
• 09 572 1394
• Email: liam@veltrimora.co.nz
• www.veltrimora.co.nz
• Address: 14 Marlow Crest Road
• Halbrook West
• Auckland 0793
Nice to have
• We would like our business cards to have more than just two colours as we want them to be more vibrant. We have uploaded an example of a business card we liked that showed this.

```html
<!DOCTYPE html>
<html lang="en">
<head>
<meta charset="utf-8">
<title>Veltrimora business card</title>
<link rel="stylesheet" href="https://fonts.googleapis.com/css2?family=Open+Sans:ital,wght@0,400;0,600;0,700;1,400&display=swap">
<style>
  :root {
    --brand-blue: #0a6bb8;
    --deep-blue: #0255a3;
    --grey: #919191;
    --paper: #ffffff;
    --backdrop: #2a2a2a;
    --dots: #5a6f86;
    --note-grey: #555555;
  }
  * { margin: 0; padding: 0; box-sizing: border-box; }
  html, body {
    width: 1200px; height: 987px; overflow: hidden;
    background: var(--backdrop);
    font-family: "Open Sans", Arial, sans-serif;
  }
  .canvas { position: relative; width: 1200px; height: 987px; }
  .card {
    position: absolute; left: 293px; width: 615px; height: 352px;
    background: var(--paper); overflow: hidden;
  }
  .card--front { top: 130px; }
  .card--back { top: 505px; }

  .wave { position: absolute; inset: 0; width: 100%; height: 100%; }

  .brand {
    position: absolute; left: 319px; top: 41px; width: 260px;
    display: flex; flex-direction: column; align-items: center;
  }
  .brand__square { width: 55px; height: 52px; background: var(--brand-blue); }
  .brand__name {
    margin-top: 8px; color: var(--brand-blue);
    font-size: 27px; font-weight: 400; letter-spacing: 1.5px; line-height: 1;
  }

  .technician {
    position: absolute; left: 22px; top: 143px; color: var(--paper);
  }
  .technician__name { font-size: 17.5px; font-weight: 700; line-height: 25px; }
  .technician__role { font-size: 16px; line-height: 25px; margin-bottom: 3px; }
  .contact { list-style: none; font-size: 15px; line-height: 23.5px; }
  .contact li { display: flex; align-items: center; gap: 6px; }
  .contact svg { width: 16px; height: 16px; fill: var(--paper); flex: none; }
  .technician__address { font-size: 15.5px; margin-top: 5px; }

  .appointment { padding: 30px 34px 0 30px; color: var(--brand-blue); }
  .appointment__title {
    text-align: center; font-size: 23px; font-weight: 600; margin-bottom: 20px;
  }
  .field { display: flex; align-items: baseline; font-size: 16.5px; }
  .field__line { flex: 1; border-bottom: 2px dotted var(--dots); margin-left: 6px; height: 1px; }
  .field--name { margin-left: 3px; margin-bottom: 22px; }
  .field-row { display: flex; align-items: baseline; margin-bottom: 27px; }
  .field--date { width: 292px; }
  .field--time { flex: 1; margin-left: 20px; }
  .field__suffix { font-size: 13px; margin-left: 8px; }
  .days { display: flex; justify-content: space-between; font-size: 15px; margin: 0 0 22px 3px; }
  .day { display: flex; align-items: center; gap: 5px; }
  .day__box { width: 16px; height: 13px; border: 1.5px solid var(--brand-blue); }
  .field--note { margin-left: 4px; margin-bottom: 22px; }
  .field--blank .field__line { margin-left: 4px; }
  .appointment__policy {
    margin-top: 30px; text-align: center; font-style: italic;
    font-size: 12.5px; line-height: 18px; color: var(--note-grey);
  }
</style>
</head>
<body>
<main class="canvas">
  <section class="card card--front" aria-label="Card front">
    <svg class="wave" viewBox="0 0 615 352" preserveAspectRatio="none" aria-hidden="true">
      <path d="M0,100 C55,70 125,72 225,145 C330,222 420,300 520,292 C560,288 595,275 615,262 L615,352 L0,352 Z" fill="var(--brand-blue)"/>
      <path d="M0,92 C55,60 125,64 230,138" fill="none" stroke="var(--brand-blue)" stroke-width="2"/>
      <path d="M40,84 C110,70 175,98 250,160 C340,235 420,300 530,290 C560,287 580,282 590,278" fill="none" stroke="var(--paper)" stroke-width="2.5"/>
    </svg>

    <div class="brand">
      <div class="brand__square"></div>
      <div class="brand__name">VELTRIMORA</div>
    </div>

    <div class="technician">
      <p class="technician__name">Liam Dorsett BDT,<br>PGDipCDentTech Calverin</p>
      <p class="technician__role">Dental Prosthetist</p>
      <ul class="contact">
        <li><svg viewBox="0 0 16 16"><path d="M1 6c2-4 12-4 14 0l-3 1.5-1-2H5L4 7.5 1 6zm3 2h8l1 6H3l1-6zm4 1.5a2 2 0 1 0 0 4 2 2 0 0 0 0-4z"/></svg>0800 47 3125</li>
        <li><svg viewBox="0 0 16 16"><path d="M4.5 0h7a1 1 0 0 1 1 1v14a1 1 0 0 1-1 1h-7a1 1 0 0 1-1-1V1a1 1 0 0 1 1-1zm.5 2v10h6V2H5zm3 11a1 1 0 1 0 0 2 1 1 0 0 0 0-2z"/></svg>09 572 1394</li>
        <li><svg viewBox="0 0 16 16"><path d="M1 3h14v1L8 9 1 4V3zm0 2.5 7 5 7-5V13H1V5.5z"/></svg>liam@veltrimora.co.nz</li>
        <li><svg viewBox="0 0 16 16"><circle cx="8" cy="8" r="7.5"/><path d="M5 4l3 2-1 2 3 2-1 3" stroke="var(--brand-blue)" stroke-width="1.4" fill="none"/></svg>www.veltrimora.co.nz</li>
      </ul>
      <p class="technician__address">14 Marlow Crest Road, Halbrook West, Auckland 0793</p>
    </div>
  </section>

  <section class="card card--back" aria-label="Card back">
    <div class="appointment">
      <h2 class="appointment__title">Next Appointment</h2>
      <div class="field field--name">Name :<span class="field__line"></span></div>
      <div class="field-row">
        <div class="field field--date">Date :<span class="field__line"></span></div>
        <div class="field field--time">Time :<span class="field__line"></span><span class="field__suffix">AM/PM</span></div>
      </div>
      <div class="days">
        <span class="day">Sun<span class="day__box"></span></span>
        <span class="day">Mon<span class="day__box"></span></span>
        <span class="day">Tue<span class="day__box"></span></span>
        <span class="day">Wed<span class="day__box"></span></span>
        <span class="day">Thu<span class="day__box"></span></span>
        <span class="day">Fri<span class="day__box"></span></span>
        <span class="day">Sat<span class="day__box"></span></span>
      </div>
      <div class="field field--note">Note :<span class="field__line"></span></div>
      <div class="field field--blank"><span class="field__line"></span></div>
      <p class="appointment__policy">Please give me 24 hours notice if you are unable to keep your appointment or<br>a cancellation fee may be charged.</p>
    </div>
  </section>
</main>
</body>
</html>
```